Recipe Card Design

I have a small kitchen store in Livingston Montana, and I would like to have recipe cards (4x6 postcard) designed with my logo, lines for recipe writing, all in black and white. My website is here: www.brambleforkcookware.com

Store

```html
<!DOCTYPE html>
<html lang="en">
<head>
<meta charset="utf-8">
<title>Bramble Fork Cookware – Hours Card and Recipe Card</title>
<link href="https://fonts.googleapis.com/css2?family=IM+Fell+English+SC&family=Patrick+Hand&family=Amatic+SC:wght@700&display=swap" rel="stylesheet">
<style>
  :root {
    --board: #1f1f1f;
    --board-edge: #151515;
    --chalk: #f4f4f0;
    --paper: #ffffff;
    --ink: #1a1a1a;
    --rule: #8c8c8c;
    --backdrop: #d8d3cb;
  }
  html, body {
    margin: 0;
    width: 1200px;
    height: 1200px;
    overflow: hidden;
    background: var(--backdrop);
  }
  .canvas { position: relative; width: 1200px; height: 1200px; }

  .card {
    position: absolute;
    background: radial-gradient(circle at 40% 30%, #2a2a2a, var(--board) 70%, var(--board-edge));
    color: var(--chalk);
    box-shadow: 0 6px 18px rgba(0,0,0,.35);
  }

  /* ---------- Hours card ---------- */
  .hours-card { left: 40px; top: 40px; width: 460px; height: 690px; }
  .icon-strip {
    position: absolute; left: 14px; top: 40px; width: 44px; height: 610px;
    background: linear-gradient(180deg, #d9d9d9, #9a9a9a 50%, #d9d9d9);
    opacity: .85; border-radius: 6px;
  }
  .strip-rule {
    position: absolute; left: 70px; top: 0; height: 690px;
    border-left: 3px dotted var(--chalk);
  }
  .hours-content { position: absolute; left: 90px; top: 0; width: 350px; height: 690px; text-align: center; }
  .brand {
    font-family: "IM Fell English SC", serif;
    color: var(--chalk);
  }
  .hours-card .brand { position: absolute; top: 70px; left: 0; width: 350px; }
  .brand-name { font-size: 46px; line-height: 1; display: block; white-space: nowrap; }
  .brand-name.sub { font-size: 30px; margin-top: 8px; }
  .brand-place { font-size: 15px; letter-spacing: 4px; display: block; margin-top: 12px; white-space: nowrap; }
  .brand-mark {
    width: 14px; height: 14px; border-radius: 50%; background: var(--chalk);
    display: inline-block; margin-bottom: 10px;
  }

  .section-title {
    position: absolute; left: 0; width: 350px; margin: 0;
    display: flex; align-items: center; gap: 12px;
    font-family: "IM Fell English SC", serif; font-size: 36px; font-weight: 400;
  }
  .section-title::before, .section-title::after {
    content: ""; flex: 1; border-top: 3px dotted var(--chalk);
  }
  .hours-title { top: 250px; }
  .location-title { top: 520px; }

  .hours-table {
    position: absolute; top: 310px; left: 10px; width: 330px; height: 190px;
    display: flex; gap: 8px;
    font-family: "Patrick Hand", cursive; font-size: 21px; line-height: 29px;
  }
  .hours-days, .hours-times {
    border: 1.5px dashed var(--chalk); border-radius: 10px;
    padding: 7px 10px; list-style: none; margin: 0; text-align: left;
  }
  .hours-days { width: 110px; }
  .hours-times { flex: 1; text-align: center; }

  .location-details {
    position: absolute; top: 578px; left: 0; width: 350px; font-style: normal;
    font-family: "Patrick Hand", cursive; font-size: 18px; line-height: 24px;
  }
  .location-details .phone { font-size: 21px; }
  .location-details .web { font-size: 13px; letter-spacing: .5px; }
  .bottom-rule { position: absolute; top: 662px; left: 0; width: 350px; border-top: 3px dotted var(--chalk); }

  /* ---------- Recipe card ---------- */
  .recipe-card { left: 520px; top: 745px; width: 640px; height: 427px; }
  .recipe-card .brand { position: absolute; left: 10px; top: 26px; width: 170px; text-align: center; }
  .recipe-card .brand-name { font-size: 24px; }
  .recipe-card .brand-name.sub { font-size: 18px; margin-top: 4px; }
  .recipe-card .brand-place { font-size: 8px; letter-spacing: 1.5px; margin-top: 8px; }
  .recipe-card .brand-mark { width: 10px; height: 10px; margin-bottom: 6px; }

  .recipe-label {
    position: absolute; left: 18px; top: 288px; width: 130px;
    transform: rotate(-90deg); transform-origin: left top;
    font-family: "Amatic SC", sans-serif; font-weight: 700; font-size: 64px;
    letter-spacing: 3px; line-height: 64px; white-space: nowrap;
  }
  .ribbon { position: absolute; left: 100px; top: 176px; width: 40px; height: 236px; }
  .utensils {
    position: absolute; left: 24px; top: 300px; width: 54px; height: 54px;
    background: linear-gradient(135deg, #e6e6e6, #a9a9a9); border-radius: 4px;
  }
  .pie {
    position: absolute; left: 20px; top: 366px; width: 62px; height: 40px;
    background: radial-gradient(ellipse, #e8e8e8, #9d9d9d); border-radius: 50%;
  }

  .write-box {
    position: absolute; left: 200px; width: 410px;
    background: var(--paper); color: var(--ink);
    border: 4px dotted var(--paper); background-clip: padding-box;
    border-radius: 14px; outline: 2px solid var(--paper); outline-offset: -10px;
  }
  .ingredients-box { top: 16px; height: 160px; }
  .instruction-box { top: 206px; height: 196px; }
  .write-title {
    font-family: "IM Fell English SC", serif; font-size: 24px; font-weight: 400;
    text-align: center; margin: 12px 0 4px;
  }
  .write-lines { margin: 0 22px; }
  .instruction-box .write-lines { margin-right: 86px; }
  .write-line { height: 16px; border-bottom: 1.5px dotted var(--rule); }
  .box-divider { position: absolute; left: 170px; top: 190px; width: 452px; border-top: 3px dotted var(--chalk); }
  .grater-mitt {
    position: absolute; right: 14px; bottom: 12px; width: 56px; height: 76px;
    background: linear-gradient(160deg, #5a5a5a, #1d1d1d); border-radius: 6px;
  }
</style>
</head>
<body>
<main class="canvas">

  <section class="card hours-card" aria-label="Store hours and location card">
    <div class="icon-strip" role="img" aria-label="Column of small kitchen and baking illustrations: cupcake, cake slice, jelly mould, muffin tin, pancakes, oven mitt, grater, utensils, pie"></div>
    <div class="strip-rule"></div>

    <div class="hours-content">
      <div class="brand">
        <span class="brand-mark"></span>
        <span class="brand-name">Bramble Fork</span>
        <span class="brand-name sub">Cookware</span>
        <span class="brand-place">LARKSPUR FALLS, MONTANA</span>
      </div>

      <h2 class="section-title hours-title">Hours</h2>
      <div class="hours-table">
        <ul class="hours-days">
          <li>Monday:</li><li>Tuesday:</li><li>Wednesday:</li>
          <li>Thursday:</li><li>Friday:</li><li>Saturday:</li>
        </ul>
        <ul class="hours-times">
          <li>10:00 am - 5:00 pm</li><li>10:00 am - 5:00 pm</li><li>10:00 am - 5:00 pm</li>
          <li>10:00 am - 5:00 pm</li><li>10:00 am - 5:00 pm</li><li>10:00 am - 2:30 pm</li>
        </ul>
      </div>

      <h2 class="section-title location-title">Location</h2>
      <address class="location-details">
        <div>218 North Larch Avenue, Larkspur Falls, MT 59099</div>
        <div class="phone">(406) 555-0148</div>
        <div class="web">WWW.BRAMBLEFORKCOOKWARE.COM</div>
      </address>
      <div class="bottom-rule"></div>
    </div>
  </section>

  <section class="card recipe-card" aria-label="Recipe card">
    <div class="brand">
      <span class="brand-mark"></span>
      <span class="brand-name">Bramble Fork</span>
      <span class="brand-name sub">Cookware</span>
      <span class="brand-place">LARKSPUR FALLS, MONTANA</span>
    </div>

    <div class="recipe-label">RECEPE</div>
    <svg class="ribbon" viewBox="0 0 40 236" aria-hidden="true">
      <polygon points="0,0 40,8 40,236 20,222 0,236" fill="#ffffff"/>
    </svg>
    <div class="utensils" role="img" aria-label="Crossed fork and spoon illustration"></div>
    <div class="pie" role="img" aria-label="Lattice pie illustration"></div>

    <div class="write-box ingredients-box">
      <h3 class="write-title">Ingredients</h3>
      <div class="write-lines">
        <div class="write-line"></div><div class="write-line"></div><div class="write-line"></div>
        <div class="write-line"></div><div class="write-line"></div><div class="write-line"></div>
      </div>
    </div>

    <div class="box-divider"></div>

    <div class="write-box instruction-box">
      <h3 class="write-title">Instruction</h3>
      <div class="write-lines">
        <div class="write-line"></div><div class="write-line"></div><div class="write-line"></div>
        <div class="write-line"></div><div class="write-line"></div><div class="write-line"></div>
        <div class="write-line"></div><div class="write-line"></div>
      </div>
      <div class="grater-mitt" role="img" aria-label="Box grater and oven mitt illustration"></div>
    </div>
  </section>

</main>
</body>
</html>
```